Non Profit Company Looking For New Website

The website for Fernvale Quillstone Heritage Society should offer the viewer beautiful photos that inspire condifence and joy and tap into our love of horses.

We would like to see a website that displays trust, quality and confidence. Needs to be responsive and mobile friendly for all browsers and coded for both Android & IOS.

READ ATTACHED WEBSITE TEMPLATE FOR COMPLETE DETAILS ON WHAT WE ARE LOOKING FOR.

Looking for recommmendations if we should use WordPress/WooCommerce for site or Wordpress with Shopify Plug in or just Shopify.

Must be both desktop and mobile friendly with fast page load speed. Need the ability to edit ourselves.

Industry/Entity Type

Non Profit

Coding

Coded - Design and coding required

Number of Pages Required

5+ page

Requirements
Must have
• We would like to see a website that displays trust, quality and confidence. Needs to be responsive and mobile friendly for all browsers and coded for both Android & IOS.

Looking for recommendations if we should use WordPress/WooCommerce for site or Wordpress with Shopify Plug in or just Shopify.

Logo Colour:
Pantone 7621 C

READ TEMPLATE THAT IS ATTACHED
Nice to have
• Like look of this website as a sample:
https://www.quellbrimtorva.com/

Another similar non profit organization
https://pellaworthcindle.com/

```html
<!DOCTYPE html>
<html lang="en">
<head>
<meta charset="utf-8">
<title>Fernvale Quillstone Heritage Society</title>
<link href="https://fonts.googleapis.com/css2?family=Cinzel:wght@600;700&family=Montserrat:wght@400;500;600&display=swap" rel="stylesheet">
<style>
  :root {
    --brand-red: #c0202f;
    --ink: #222222;
    --white: #ffffff;
    --soft-grey: #f8f8f8;
    --footer-dark: #1f1f1f;
    --line-grey: #555555;
    --serif: "Cinzel", "Times New Roman", serif;
    --sans: "Montserrat", Arial, sans-serif;
  }
  * { box-sizing: border-box; margin: 0; padding: 0; }
  html, body { width: 1200px; height: 3328px; overflow: hidden; }
  body { position: relative; font-family: var(--sans); color: var(--ink); background: var(--white); }
  .abs { position: absolute; }

  /* Header */
  .site-header { position: absolute; left: 0; top: 0; width: 1200px; height: 107px; background: var(--white); z-index: 3; }
  .nav-link { position: absolute; top: 46px; font-size: 13px; font-weight: 500; letter-spacing: 0.4px; color: var(--ink); text-decoration: none; }
  .brand-badge { position: absolute; left: 462px; top: -60px; width: 276px; height: 276px; border-radius: 50%; background: var(--white); z-index: 4; display: flex; align-items: flex-end; justify-content: center; padding-bottom: 52px; }
  .brand-name { font-family: var(--serif); font-weight: 700; color: var(--brand-red); font-size: 22px; line-height: 1.2; text-align: center; letter-spacing: 0.5px; }

  /* Hero */
  .hero { position: absolute; left: 0; top: 107px; width: 1200px; height: 614px;
    background: linear-gradient(180deg, #4e5356 0%, #8b8a83 30%, #a8a27f 52%, #8a8f4c 70%, #6b7a35 100%); }
  .hero-glow { position: absolute; right: 120px; top: 150px; width: 420px; height: 260px; border-radius: 50%;
    background: radial-gradient(ellipse at center, rgba(255,236,200,0.55), rgba(255,236,200,0) 70%); }
  .hero-rider { position: absolute; left: 700px; top: 150px; width: 380px; height: 330px; border-radius: 40% 50% 45% 40%;
    background: radial-gradient(ellipse at center, rgba(110,62,36,0.85), rgba(110,62,36,0) 70%); }
  .hero-lead { position: absolute; left: 173px; top: 318px; width: 560px; color: var(--white); font-size: 18px; line-height: 32px; font-weight: 500; }
  .hero-title { position: absolute; left: 173px; top: 406px; color: var(--white); font-family: var(--serif); font-weight: 700; font-size: 44px; letter-spacing: 0.5px; }
  .hero-note { position: absolute; left: 173px; top: 490px; width: 560px; color: var(--white); font-size: 18px; line-height: 32px; font-weight: 500; }

  /* Shared */
  .section-title { font-family: var(--serif); font-weight: 700; color: var(--brand-red); font-size: 35px; line-height: 40px; }
  .btn { position: absolute; display: flex; align-items: center; justify-content: center; background: var(--brand-red); color: var(--white); font-weight: 600; text-transform: uppercase; letter-spacing: 0.3px; text-decoration: none; }

  /* About */
  .about-title { position: absolute; left: 173px; top: 812px; width: 520px; }
  .about-text { position: absolute; left: 173px; top: 916px; width: 493px; font-size: 12.2px; line-height: 25.6px; text-align: justify; }
  .about-mark { position: absolute; left: 700px; top: 820px; width: 360px; height: 300px; display: flex; align-items: center; justify-content: center; gap: 16px; }
  .about-mark .dot { width: 46px; height: 46px; border-radius: 50%; background: var(--brand-red); flex: none; }
  .about-mark .brand-name { font-size: 30px; text-align: left; }

  /* Adopt */
  .adopt { position: absolute; left: 0; top: 1241px; width: 1200px; height: 902px; background: var(--soft-grey); }
  .adopt-title { position: absolute; left: 0; width: 1200px; top: 70px; text-align: center; }
  .adopt-sub { position: absolute; left: 0; width: 1200px; top: 133px; text-align: center; font-size: 13.5px; }
  .horse-card { position: absolute; width: 275px; height: 245px; background: var(--white); padding: 3px; box-shadow: 0 0 6px rgba(0,0,0,0.18); }
  .horse-card .photo { width: 100%; height: 100%; }

  /* Difference */
  .difference { position: absolute; left: 0; top: 2143px; width: 1200px; height: 607px;
    background: linear-gradient(90deg, #8a4a26 0%, #6d5236 30%, #3b4b34 55%, #2c4232 75%, #3a4a30 100%); }
  .difference-photo-shade { position: absolute; left: 0; top: 0; width: 1200px; height: 607px;
    background: linear-gradient(180deg, rgba(0,0,0,0) 60%, rgba(120,140,70,0.45) 100%); }
  .difference-title { position: absolute; left: 663px; top: 150px; font-family: var(--serif); font-weight: 700; color: var(--white); font-size: 32px; }
  .difference-text { position: absolute; left: 660px; top: 224px; width: 367px; color: var(--white); font-size: 13.4px; line-height: 25.6px; text-align: justify; }

  /* Footer */
  .site-footer { position: absolute; left: 0; top: 2750px; width: 1200px; height: 578px; background: var(--footer-dark); color: var(--white); }
  .contact-icon { position: absolute; left: 173px; width: 53px; height: 53px; border-radius: 50%; background: var(--white); display: flex; align-items: center; justify-content: center; }
  .contact-label { position: absolute; left: 243px; font-size: 15px; font-weight: 600; }
  .contact-value { position: absolute; left: 243px; font-size: 20px; font-weight: 600; line-height: 27px; }
  .field { position: absolute; background: var(--white); color: #333; font-size: 14px; padding: 15px 10px; }
  .footer-rule { position: absolute; left: 173px; top: 483px; width: 854px; height: 1px; background: var(--line-grey); }
  .copyright { position: absolute; left: 0; width: 1200px; top: 519px; text-align: center; font-size: 14px; font-weight: 500; }
</style>
</head>
<body>

<header class="site-header">
  <a class="nav-link" style="left:171px" href="#">HOME</a>
  <a class="nav-link" style="left:253px" href="#">ABOUT</a>
  <a class="nav-link" style="left:340px" href="#">ADOPT</a>
  <a class="nav-link" style="left:768px" href="#">HORSES</a>
  <a class="nav-link" style="left:863px" href="#">DONATE</a>
  <a class="nav-link" style="left:961px" href="#">CONTACT</a>
</header>
<div class="brand-badge"><div class="brand-name">Fernvale<br>Quillstone<br>Heritage Society</div></div>

<section class="hero" role="img" aria-label="Photo of a jockey galloping a thoroughbred racehorse across a grass field at sunset">
  <div class="hero-glow"></div>
  <div class="hero-rider"></div>
</section>
<p class="hero-lead">We support and develop retired thoroughbred racehorses for their next chapter in life.</p>
<h1 class="hero-title">RETIRE. RETRAIN. REHOME.</h1>
<p class="hero-note">Fernvale Quillstone Heritage Society (FQHS) is a registered not-for-profit organization in Fernvale.</p>

<h2 class="section-title about-title">WHAT IS THOROUGHBRED AFTERCARE?</h2>
<p class="about-text">The health, safety and welfare of our equine athletes does not end at the finish line, and retirement and aftercare are critical to the success of the racing industry. After care is the safe placement of racehorses after their careers as racehorse are completed. Some horses might retire to the breeding shed or broodmare bands, while others are retrained for second careers.</p>
<a class="btn" style="left:173px;top:1068px;width:178px;height:58px;font-size:12.5px" href="#">Learn more about us</a>
<div class="about-mark"><span class="dot"></span><span class="brand-name">Fernvale<br>Quillstone<br>Heritage Society</span></div>

<section class="adopt">
  <h2 class="section-title adopt-title">ADOPT A HORSE</h2>
  <p class="adopt-sub">Fernvale Quillstone Heritage Society is committed to helping match you with the perfect horse.</p>

  <div class="horse-card" style="left:173px;top:206px"><div class="photo" role="img" aria-label="Jockey riding a bay racehorse at full gallop" style="background:linear-gradient(160deg,#54534f,#8b725a 55%,#c7a77c)"></div></div>
  <div class="horse-card" style="left:463px;top:206px"><div class="photo" role="img" aria-label="Jockey on a grey horse along the rail in front of a crowd" style="background:linear-gradient(180deg,#3e4a4a,#5b5f55 55%,#6f8a3e)"></div></div>
  <div class="horse-card" style="left:752px;top:206px"><div class="photo" role="img" aria-label="Two racehorses with jockeys near the track rail" style="background:linear-gradient(180deg,#3f4a4c,#6a5a48 55%,#6f8a3e)"></div></div>
  <div class="horse-card" style="left:173px;top:468px"><div class="photo" role="img" aria-label="Group of racehorses running on a grass track" style="background:linear-gradient(180deg,#4f6b3a,#5a4b3a 55%,#6f8f3d)"></div></div>
  <div class="horse-card" style="left:463px;top:468px"><div class="photo" role="img" aria-label="Two jockeys racing chestnut horses side by side" style="background:linear-gradient(160deg,#3c4650,#7f5b40 55%,#c7a77c)"></div></div>
  <div class="horse-card" style="left:752px;top:468px"><div class="photo" role="img" aria-label="Jockey galloping a horse on a dirt training track" style="background:linear-gradient(180deg,#e2e2e0,#6f7d55 40%,#c2a98a)"></div></div>

  <a class="btn" style="left:528px;top:765px;width:144px;height:58px;font-size:15px" href="#">Adopt now</a>
</section>

<section class="difference" role="img" aria-label="Photo of a woman resting her head against a chestnut horse in a green meadow">
  <div class="difference-photo-shade"></div>
  <h2 class="difference-title">MAKE A DIFFERENCE</h2>
  <p class="difference-text">Fernvale Quillstone Heritage Society has a committed group of individuals who are working together to create a registered charity for thoroughbred aftercare. We are passionate about the welfare of thoroughbred race horses both on, and off the track.</p>
  <a class="btn" style="left:660px;top:385px;width:200px;height:59px;font-size:15px" href="#">More ways to give</a>
</section>

<footer class="site-footer">
  <div class="contact-icon" style="top:146px">
    <svg width="24" height="24" viewBox="0 0 24 24" fill="none" stroke="#333" stroke-width="1.5" stroke-linejoin="round"><path d="M5 3h4l2 5-2.5 1.5a11 11 0 0 0 6 6L16 13l5 2v4a2 2 0 0 1-2 2A16 16 0 0 1 3 5a2 2 0 0 1 2-2z"/></svg>
  </div>
  <div class="contact-label" style="top:151px">Call Us At:</div>
  <div class="contact-value" style="top:170px">+1 555 014 2290</div>

  <div class="contact-icon" style="top:229px">
    <svg width="24" height="24" viewBox="0 0 24 24" fill="none" stroke="#333" stroke-width="1.6"><rect x="3" y="6" width="18" height="12"/><path d="M3 6l9 7 9-7"/></svg>
  </div>
  <div class="contact-label" style="top:234px">Mail Us At:</div>
  <div class="contact-value" style="top:253px">info@fernvalequillstone.org</div>

  <div class="contact-icon" style="top:312px">
    <svg width="24" height="24" viewBox="0 0 24 24" fill="none" stroke="#333" stroke-width="1.6"><path d="M12 22s7-7 7-12a7 7 0 0 0-14 0c0 5 7 12 7 12z"/><circle cx="12" cy="10" r="2.5"/></svg>
  </div>
  <div class="contact-label" style="top:316px">Address:</div>
  <div class="contact-value" style="top:335px">25, Dummy City, Street,<br>Town - 123</div>

  <div class="field" style="left:557px;top:120px;width:230px;height:53px">Name</div>
  <div class="field" style="left:797px;top:120px;width:230px;height:53px">Phone</div>
  <div class="field" style="left:557px;top:183px;width:470px;height:53px">Email</div>
  <div class="field" style="left:557px;top:248px;width:470px;height:90px">Message</div>
  <a class="btn" style="left:557px;top:359px;width:126px;height:53px;font-size:15px" href="#">Submit</a>

  <div class="footer-rule"></div>
  <p class="copyright">Copyrights @ 2021 Fernvale. All Rights Reserved.</p>
</footer>

</body>
</html>
```